Business Card for Coastal Tundrabridge Advisory

We need a business card for Coastal Tundrabridge Advisory. The company website address is provided below. The company logo is attached. We provide specialized permafrost services to the mining, transportation, and oil & gas industries. The card should be prepared for:
Matthias Korhonen, PhD.
Coastal Tundrabridge Advisory
PO Box 418259
Quillwater, Alaska 99642
Direct: +1-907-555-0143
Email: mkorhonen@tundrabridgeadvisory.example
Website: www.coastaltundrabridgeadvisory.example

```html
<!DOCTYPE html>
<html lang="en">
<head>
<meta charset="utf-8">
<title>Coastal Tundrabridge Advisory – Business Card</title>
<link rel="stylesheet" href="https://fonts.googleapis.com/css2?family=Heebo:wght@300;400;500;700&display=swap">
<style>
  :root {
    --backdrop: #222222;
    --card: #111722;
    --ink: #f4f5f7;
    --ink-soft: #c9ccd3;
    --rule: #8a8f99;
  }
  * { margin: 0; padding: 0; box-sizing: border-box; }
  html, body {
    width: 1200px;
    height: 780px;
    overflow: hidden;
    background: var(--backdrop);
    font-family: "Heebo", Arial, sans-serif;
    color: var(--ink);
  }
  .canvas {
    position: relative;
    width: 1200px;
    height: 780px;
    display: flex;
    align-items: center;
    justify-content: center;
    gap: 40px;
  }
  .card {
    position: relative;
    width: 540px;
    height: 309px;
    background: var(--card);
    border-radius: 3px;
    box-shadow: 0 10px 30px rgba(0,0,0,0.45);
    overflow: hidden;
  }

  /* Contact side */
  .person {
    position: absolute;
    left: 42px;
    top: 58px;
    width: 215px;
    text-align: right;
  }
  .person-name {
    font-size: 25px;
    line-height: 1.15;
    letter-spacing: -0.2px;
  }
  .person-name .given { font-weight: 700; }
  .person-name .family { font-weight: 300; }
  .person-title {
    font-size: 15px;
    font-weight: 700;
    margin-top: 4px;
  }
  .divider {
    position: absolute;
    left: 272px;
    top: 112px;
    width: 1px;
    height: 92px;
    background: var(--rule);
  }
  .contacts {
    position: absolute;
    left: 288px;
    top: 122px;
    list-style: none;
  }
  .contacts li {
    display: flex;
    align-items: center;
    gap: 7px;
    font-size: 11.5px;
    font-weight: 400;
    line-height: 1;
    margin-bottom: 11px;
    white-space: nowrap;
  }
  .contacts svg { width: 12px; height: 12px; flex: none; }
  .address {
    position: absolute;
    left: 42px;
    bottom: 34px;
    width: 215px;
    text-align: right;
    font-size: 12px;
    font-weight: 400;
    color: var(--ink-soft);
    line-height: 1.45;
  }

  /* Brand side */
  .brand {
    position: absolute;
    left: 0;
    right: 0;
    top: 70px;
    text-align: center;
  }
  .brand-name {
    font-size: 30px;
    font-weight: 700;
    text-transform: uppercase;
    letter-spacing: 3px;
    line-height: 1.2;
    color: var(--ink);
  }
  .services {
    position: absolute;
    left: 24px;
    right: 24px;
    bottom: 30px;
    text-align: center;
  }
  .services-heading {
    font-size: 11px;
    font-weight: 700;
    text-transform: uppercase;
    letter-spacing: 0.3px;
    margin-bottom: 5px;
  }
  .services-text {
    font-size: 11px;
    font-weight: 300;
    font-style: italic;
    color: var(--ink-soft);
  }
</style>
</head>
<body>
<main class="canvas">

  <section class="card card-contact" aria-label="Contact side">
    <div class="person">
      <p class="person-name"><span class="given">Matthias</span> <span class="family">Korhonen</span></p>
      <p class="person-title">PhD</p>
    </div>

    <div class="divider"></div>

    <ul class="contacts">
      <li>
        <svg viewBox="0 0 24 24" aria-hidden="true"><path fill="#f4f5f7" d="M6.6 10.8a15.1 15.1 0 0 0 6.6 6.6l2.2-2.2a1 1 0 0 1 1-.25 11.4 11.4 0 0 0 3.6.57 1 1 0 0 1 1 1V20a1 1 0 0 1-1 1A17 17 0 0 1 3 4a1 1 0 0 1 1-1h3.5a1 1 0 0 1 1 1c0 1.25.2 2.45.57 3.57a1 1 0 0 1-.25 1z"/></svg>
        +1-907-555-0143
      </li>
      <li>
        <svg viewBox="0 0 24 24" aria-hidden="true"><rect x="2.5" y="5" width="19" height="14" rx="1.5" fill="none" stroke="#f4f5f7" stroke-width="2"/><path d="M3 6l9 7 9-7" fill="none" stroke="#f4f5f7" stroke-width="2"/></svg>
        mkorhonen@tundrabridgeadvisory.example
      </li>
      <li>
        <svg viewBox="0 0 24 24" aria-hidden="true"><circle cx="12" cy="12" r="9.5" fill="none" stroke="#f4f5f7" stroke-width="2"/><ellipse cx="12" cy="12" rx="4" ry="9.5" fill="none" stroke="#f4f5f7" stroke-width="1.6"/><path d="M2.5 12h19" stroke="#f4f5f7" stroke-width="1.6"/></svg>
        www.coastaltundrabridgeadvisory.example
      </li>
    </ul>

    <p class="address">PO Box 418259<br>Quillwater, Alaska 99642</p>
  </section>

  <section class="card card-brand" aria-label="Brand side">
    <div class="brand">
      <p class="brand-name">Coastal Tundrabridge<br>Advisory</p>
    </div>
    <div class="services">
      <p class="services-heading">Our Services</p>
      <p class="services-text">We provide specialized permafrost services to the mining, transportation, and oil &amp; gas industries</p>
    </div>
  </section>

</main>
</body>
</html>
```